Pebblebrook Plots - Online-only garden installation company

Online-only garden installation company. Our demographic is middle aged / suburban women, and we anticipate Facebook driving traffic to this website, as well as referrals from garden centers. The website must be very simple in design and function.

All orders will be placed through the website, including size of garden (3 options), location in yard, payment, and scheduling of installation date.

The website should employ a 3 step process:

Step 1: Select garden size. Either an 4' X 4', 8' X 4', or 12' X 4'.

Step 2: Select a location. We would like to use google maps to look up a US address, then "drag and drop" one of the garden sizes from step 1 to the location the customer would like us to install the garden at their home.

Step 3: Pick an installation date and pay. Using an online calendar the customer will pick a date, and then pay for the installation via credit card.

The website will be linked to an email account, PebblebrookPlots@mailvale.com to inform us of orders placed.

Target Market(s)

Our demographic is middle aged / suburban women, and we anticipate Facebook driving traffic to this website, as well as referrals from garden centers.

Industry/Entity Type

Coding

Number of Pages Required

Requirements
Must have
• Scheduling and payment options.

```html
<!DOCTYPE html>
<html lang="en">
<head>
<meta charset="utf-8">
<title>Pebblebrook Plots</title>
<link href="https://fonts.googleapis.com/css2?family=Catamaran:wght@500;600;700&family=Open+Sans:wght@400;600;700&display=swap" rel="stylesheet">
<style>
:root{
  --green:#3a853b;
  --orange:#e0562b;
  --ink:#444;
  --body:#555;
  --grey-band:#ebe9e9;
  --white:#fff;
  --dark:#141a12;
}
*{box-sizing:border-box;margin:0;padding:0}
html,body{width:673px;height:1200px;overflow:hidden;background:var(--white)}
body{position:relative;font-family:"Open Sans",sans-serif;color:var(--body)}
.abs{position:absolute}

/* header */
.site-header{position:absolute;left:0;top:0;width:673px;height:108px}
.social{position:absolute;top:57px;left:54px;display:flex;gap:14px}
.social span{width:13px;height:13px;border-radius:3px;background:#333;display:block}
.social span:first-child{background:var(--orange)}
.brand{position:absolute;left:0;width:673px;top:44px;text-align:center;font-family:"Catamaran",sans-serif;font-weight:700;font-size:17px;color:#2c2c2c;letter-spacing:.5px;display:flex;justify-content:center;align-items:center;gap:6px}
.brand i{width:12px;height:12px;border-radius:50%;background:var(--orange);display:block}
.account{position:absolute;top:56px;left:524px;display:flex;align-items:center;gap:5px;font-size:9px;font-weight:600;color:var(--green)}
.cart{position:absolute;top:56px;left:602px}

/* nav */
.main-nav{position:absolute;top:108px;left:0;width:673px;height:31px;background:var(--green)}
.main-nav a{position:absolute;top:8px;color:var(--white);font-family:"Catamaran",sans-serif;font-weight:600;font-size:10.5px;text-decoration:none}

/* hero */
.hero{position:absolute;top:139px;left:0;width:673px;height:281px;background:linear-gradient(180deg,#d8c98e 0%,#7f8a4a 30%,#4f6a2c 60%,#6a5a35 100%)}
.hero-panel{position:absolute;left:142px;top:67px;width:395px;height:140px;background:rgba(40,40,30,.62);text-align:center;color:var(--white)}
.hero-panel h1{font-family:"Catamaran",sans-serif;font-weight:600;font-size:19.5px;margin-top:24px;line-height:1.2}
.hero-panel p{font-size:7.6px;font-weight:600;line-height:11.5px;margin:6px auto 0;width:310px}
.btn{display:inline-block;margin-top:6px;background:var(--orange);color:var(--white);font-family:"Catamaran",sans-serif;font-weight:600;font-size:10.5px;padding:3px 13px;border-radius:2px}
.dots{position:absolute;top:259px;left:341px;display:flex;gap:4px}
.dots span{width:7px;height:7px;border-radius:50%;background:var(--white)}
.dots span:first-child{background:var(--orange)}

/* welcome */
.welcome-photo{position:absolute;left:55px;top:442px;width:248px;height:242px;border-radius:50%;background:radial-gradient(circle at 50% 55%,#7aa04a 0%,#5b4a35 45%,#2f2a22 100%)}
.welcome-text{position:absolute;left:332px;top:490px;width:286px}
.welcome-text h2{font-family:"Catamaran",sans-serif;font-weight:600;font-size:19.5px;color:var(--orange);line-height:1.2}
.welcome-text h3{font-size:9.5px;font-weight:700;color:var(--ink);margin:5px 0 10px}
.welcome-text p{font-size:7.4px;line-height:11.6px;text-align:justify;margin-bottom:10px}

/* steps */
.steps{position:absolute;top:710px;left:0;width:673px;height:286px;background:var(--grey-band)}
.steps-title{position:absolute;top:37px;width:673px;text-align:center;font-family:"Catamaran",sans-serif;line-height:1.2}
.steps-title .lead{display:block;color:var(--orange);font-weight:600;font-size:18.5px}
.steps-title .sub{display:block;color:var(--ink);font-weight:500;font-size:17px;margin-top:2px}
.steps-intro{position:absolute;top:101px;left:115px;width:443px;text-align:center;font-size:7.4px;line-height:11.5px}
.step{position:absolute;top:152px;width:160px}
.step h4{display:flex;align-items:center;gap:6px;font-family:"Catamaran",sans-serif;font-weight:600;font-size:13.5px;color:var(--orange);height:20px}
.step p{font-size:6.6px;line-height:11.5px;margin-top:10px}
.step a{display:block;text-align:right;font-family:"Catamaran",sans-serif;font-weight:700;font-size:10px;color:var(--orange);text-decoration:none;margin-top:2px}

/* testimonials */
.testimonials{position:absolute;top:996px;left:0;width:673px;height:162px;background:radial-gradient(ellipse at 50% 45%,#3a4a2e 0%,#1e2818 55%,var(--dark) 100%)}
.testimonials h2{position:absolute;top:20px;width:673px;text-align:center;font-family:"Catamaran",sans-serif;font-weight:700;font-size:19px;letter-spacing:.5px;color:var(--orange)}
.quote-card{position:absolute;left:127px;top:60px;width:419px;height:76px;border:1px solid var(--white);background:rgba(0,0,0,.55);color:var(--white)}
.avatar-ring{position:absolute;left:16px;top:15px;width:55px;height:55px;border:1px dashed var(--white);border-radius:50%}
.avatar{position:absolute;left:5px;top:5px;width:43px;height:43px;border-radius:50%;background:linear-gradient(160deg,#c69a7c,#6e4a36)}
.quote-card p{position:absolute;left:92px;top:18px;width:300px;font-size:7.2px;line-height:11.5px;text-align:justify}
.quote-card cite{position:absolute;right:35px;top:51px;font-style:normal;font-size:7.2px}

/* footer */
.site-footer{position:absolute;top:1158px;left:0;width:673px;height:42px;background:var(--green);color:var(--white);font-size:7.6px;text-align:center;line-height:42px}
</style>
</head>
<body>

<header class="site-header">
  <div class="social">
    <span role="img" aria-label="Social link"></span>
    <span role="img" aria-label="Social link"></span>
    <span role="img" aria-label="Social link"></span>
  </div>
  <div class="brand"><i></i>Pebblebrook Plots</div>
  <div class="account">
    <svg width="12" height="12" viewBox="0 0 12 12"><circle cx="6" cy="6" r="5.2" fill="none" stroke="#3a853b" stroke-width="1.2"/><circle cx="6" cy="4.8" r="1.8" fill="#3a853b"/><path d="M2.8 9.5a3.6 3.6 0 0 1 6.4 0" fill="#3a853b"/></svg>
    My Account
  </div>
  <svg class="cart" width="16" height="14" viewBox="0 0 16 14"><path d="M1 4h12l-1.5 7h-9z" fill="none" stroke="#3a853b" stroke-width="1.4"/><path d="M4 4l2-3M10 4l-2-3" stroke="#3a853b" stroke-width="1.2"/><circle cx="13" cy="3" r="2.6" fill="#e0562b"/></svg>
</header>

<nav class="main-nav">
  <a style="left:176px">Home</a>
  <a style="left:241px">About</a>
  <a style="left:307px">Portfolio</a>
  <a style="left:383px">Order</a>
  <a style="left:448px">Contact Us</a>
</nav>

<section class="hero" role="img" aria-label="Sunlit backyard garden path with flowers and a small house">
  <div class="hero-panel">
    <h1>Build Your Well Designed Garden With Us</h1>
    <p>Lorem Ipsum is simply dummy text of the printing and typesetting industry. Lorem Ipsum has been the industry's standard dummy text ever since the 1500s</p>
    <span class="btn">Reach Us</span>
  </div>
  <div class="dots"><span></span><span></span><span></span><span></span></div>
</section>

<div class="welcome-photo" role="img" aria-label="Hands holding a seedling in soil"></div>
<section class="welcome-text">
  <h2>Welcome To Pebblebrook Plots</h2>
  <h3>Lorem Ipsum is simply dummy text</h3>
  <p>Lorem Ipsum is simply dummy text of the printing and typesetting industry. Lorem Ipsum has been the industry's standard dummy text ever since the 1500s, when an unknown printer took a galley of type and scrambled it to make a type specimen book. It has survived not only five centuries,</p>
  <p>Lorem Ipsum is simply dummy text of the printing and typesetting industry. Lorem Ipsum has been the industry's standard dummy text ever since the 1500s, when an unknown printer took a galley of type and scrambled it to make a type specimen book. It has survived not only five centuries,</p>
</section>

<section class="steps">
  <h2 class="steps-title"><span class="lead">Now Make your Gardern Look Luxurious</span><span class="sub">With 3 Simple Steps</span></h2>
  <p class="steps-intro">Lorem Ipsum is simply dummy text of the printing and typesetting industry. Lorem Ipsum has been the industry's standard dummy text ever since the 1500s, when an unknown printer took a galley of type and scramchanged.</p>

  <div class="step" style="left:55px">
    <h4><svg width="16" height="16" viewBox="0 0 16 16"><polygon points="8,1 14,4.5 14,11.5 8,15 2,11.5 2,4.5" fill="none" stroke="#e0562b" stroke-width="1.6"/><circle cx="8" cy="8" r="2.5" fill="#e0562b"/></svg>Select Garden Size</h4>
    <p>Lorem Ipsum is simply dummy text of the printing and typesetting industry. Lorem Ipsum has been the industry's standard dummy text ever since the 1500s,</p>
    <a>Choose Your Size</a>
  </div>
  <div class="step" style="left:263px">
    <h4><svg width="18" height="16" viewBox="0 0 18 16"><path d="M1 3l5-2 6 2 5-2v12l-5 2-6-2-5 2z" fill="#e0562b"/><path d="M6 1v12M12 3v12" stroke="#ebe9e9" stroke-width="1"/></svg>Select A Location</h4>
    <p>Lorem Ipsum is simply dummy text of the printing and typesetting industry. Lorem Ipsum has been the industry's standard dummy text ever since the 1500s,</p>
    <a>Choose Your Location</a>
  </div>
  <div class="step" style="left:461px">
    <h4><svg width="16" height="16" viewBox="0 0 16 16"><rect x="1.5" y="3" width="13" height="12" rx="1" fill="none" stroke="#e0562b" stroke-width="1.5"/><path d="M1.5 6h13" stroke="#e0562b" stroke-width="1.5"/><path d="M5 1v3M11 1v3" stroke="#e0562b" stroke-width="1.5"/><path d="M5 10l2 2 4-4" fill="none" stroke="#e0562b" stroke-width="1.5"/></svg>Installation Date&amp; Pay</h4>
    <p>Lorem Ipsum is simply dummy text of the printing and typesetting industry. Lorem Ipsum has been the industry's standard dummy text ever since the 1500s,</p>
    <a>Choose Your Date</a>
  </div>
</section>

<section class="testimonials" role="img" aria-label="Dim background of hands tending lettuce plants">
  <h2>TESTIMONIALS</h2>
  <div class="quote-card">
    <div class="avatar-ring"><div class="avatar" role="img" aria-label="Customer portrait"></div></div>
    <p>Lorem Ipsum is simply dummy text of the printing and typesetting industry. Lorem Ipsum has been the industry's standard dummy text ever since the 1500s</p>
    <cite>Marla, 2 Dec</cite>
  </div>
</section>

<footer class="site-footer">© 2017&nbsp; Pebblebrook. All Rights Reserved</footer>

</body>
</html>
```